Buch-/eBook-Cover für Sachbuch gesucht
Zielgruppe
We're selfpublishing nonfiction books. Interested are adults - mostly man (age range: 25-50) - who want to learn more about leadership at their workplaces.
Aufgabenstellung
The design should be clean and simple, title easy to read, good color contrast (the cover has to stand out from an white background).

```html
<!DOCTYPE html>
<html lang="en">
<head>
<meta charset="utf-8">
<title>Leadership – Book Cover</title>
<link rel="stylesheet" href="https://fonts.googleapis.com/css2?family=Bebas+Neue&family=Roboto:wght@400&display=swap">
<style>
  :root {
    --cover-blue: #01406f;
    --spot-yellow: #ffce03;
    --paper: #f4f0e8;
    --crowd-shade: #01365f;
  }
  html, body {
    margin: 0;
    padding: 0;
    width: 750px;
    height: 1200px;
    overflow: hidden;
    background: #ffffff;
  }
  .cover {
    display: block;
    width: 750px;
    height: 1200px;
  }
  .cover-bg { fill: var(--cover-blue); }
  .spotlight { fill: var(--spot-yellow); }
  .author {
    font-family: "Roboto", sans-serif;
    font-weight: 400;
    font-size: 48px;
    fill: var(--paper);
  }
  .title {
    font-family: "Bebas Neue", sans-serif;
    font-size: 306px;
    fill: var(--paper);
  }
  .subtitle {
    font-family: "Roboto", sans-serif;
    font-weight: 400;
    font-size: 47px;
    fill: var(--paper);
  }
</style>
</head>
<body>
<svg class="cover" viewBox="0 0 750 1200" xmlns="http://www.w3.org/2000/svg">
  <defs>
    <radialGradient id="crowdShade" cx="0.55" cy="0.45" r="0.6">
      <stop offset="0" stop-color="var(--crowd-shade)" stop-opacity="0.7"/>
      <stop offset="1" stop-color="var(--cover-blue)" stop-opacity="0"/>
    </radialGradient>
  </defs>

  <rect class="cover-bg" x="0" y="0" width="750" height="1200"/>

  <polygon class="spotlight" points="750,357 436,787 750,891"/>

  <rect class="crowd-area" x="0" y="740" width="445" height="265" fill="url(#crowdShade)"
        role="img" aria-label="Small silhouettes of business people walking with long shadows, the foremost one stepping into the yellow spotlight"/>

  <text class="author" x="365" y="83" text-anchor="middle" textLength="330" lengthAdjust="spacingAndGlyphs">Daniel Ashford</text>

  <text class="title title-line1" x="42" y="340" textLength="682" lengthAdjust="spacingAndGlyphs">LEADER</text>
  <text class="title title-line2" x="36" y="593" textLength="406" lengthAdjust="spacingAndGlyphs">SHIP</text>

  <text class="subtitle" x="369" y="1106" text-anchor="middle" textLength="478" lengthAdjust="spacingAndGlyphs">FOSTERING GROWTH</text>
  <text class="subtitle" x="373" y="1165" text-anchor="middle" textLength="656" lengthAdjust="spacingAndGlyphs">AND INSPIRING EXCELLENCE</text>
</svg>
</body>
</html>
```